Professional Services - letterhead / business cards

The company (velmora partners) will provide services to Investment Funds and large investors in Spain. I have recently chosen a logo that I am attaching.

I would like a simple stationary design that i could use as letter head, business cards and "with compliments" cards.

I am not quite sure which color I will mostly use for the logo, in the email signature I will probably lean towards the white background and grey letters. I am attaching my favourite options.

Target Market(s)

Large Multinationals, Investment funds and Law firms

Industry/Entity Type

Business

Requirements
Must have
• my details are:
Luis R. Abadal
Velmora Partners S.L.
Casa de Torrelumbre
Calle de Vientoalto 27
29610 Castelbruna
T: +34 (91) 387-2265
M: +34 (646) 819-054
e-mail: labadal@velmorapartners.com

```html
<!DOCTYPE html>
<html lang="en">
<head>
<meta charset="utf-8">
<title>Velmora Partners – Business Card</title>
<link rel="stylesheet" href="https://fonts.googleapis.com/css2?family=Jost:wght@400;500&display=swap">
<style>
  :root {
    --navy: #24265f;
    --grey: #a7a8ab;
    --grey-text: #7d7e82;
    --white: #ffffff;
    --canvas: #e9e9ec;
  }
  html, body {
    margin: 0;
    width: 1200px;
    height: 711px;
    overflow: hidden;
    background: var(--canvas);
    font-family: "Jost", "Futura", sans-serif;
  }
  .card {
    position: absolute;
    top: 200px;
    width: 540px;
    height: 310px;
    overflow: hidden;
    box-shadow: 0 4px 14px rgba(0,0,0,0.18);
  }
  .card--front { left: 40px; background: var(--white); }
  .card--back { left: 620px; background: var(--navy); }
  .card__wave { position: absolute; inset: 0; }
  .brand {
    position: absolute;
    font-weight: 400;
    white-space: nowrap;
    letter-spacing: 0.5px;
  }
  .card--front .brand { left: 40px; top: 52px; font-size: 44px; color: var(--navy); }
  .card--back .brand {
    left: 0; right: 0; top: 98px;
    text-align: center; font-size: 46px; color: var(--white);
  }
  .address {
    position: absolute;
    left: 40px; top: 158px;
    font-size: 14px; line-height: 18px;
    color: var(--grey-text);
  }
  .contact {
    position: absolute;
    right: 30px; top: 148px;
    text-align: right;
    color: var(--white);
  }
  .contact__name { font-size: 21px; font-weight: 500; letter-spacing: 0.5px; line-height: 24px; }
  .contact__company { font-size: 13px; line-height: 18px; margin-bottom: 6px; }
  .contact__line { font-size: 14px; line-height: 22px; }
  .contact__line svg { width: 11px; height: 11px; margin-right: 8px; vertical-align: -1px; fill: var(--white); }
  .email {
    position: absolute;
    right: 30px; bottom: 18px;
    font-size: 13px; color: var(--white);
  }
  .email svg { width: 11px; height: 9px; margin-right: 6px; vertical-align: 0; fill: var(--white); }
  .website {
    position: absolute;
    left: 0; right: 0; top: 205px;
    text-align: center;
    font-size: 14px; font-weight: 500;
    letter-spacing: 7px;
    color: var(--white);
  }
</style>
</head>
<body>
  <section class="card card--front">
    <svg class="card__wave" viewBox="0 0 540 310" aria-hidden="true">
      <path fill="var(--grey)" d="M0,252 C150,244 250,210 325,144 C395,82 470,66 540,62 L540,80 C470,84 410,100 340,158 C260,226 150,258 0,264 Z"/>
      <path fill="var(--navy)" d="M0,274 C150,266 255,232 340,166 C410,110 470,94 540,90 L540,310 L0,310 Z"/>
    </svg>
    <div class="brand">velmora partners</div>
    <div class="address">
      Casa de Torrelumbre<br>
      Calle de Vientoalto 27<br>
      29610 Castelbruna
    </div>
    <div class="contact">
      <div class="contact__name">Luis R. Abadal</div>
      <div class="contact__company">Velmora Partners S.L.</div>
      <div class="contact__line">
        <svg viewBox="0 0 12 12" aria-hidden="true"><path d="M2.5,0.5 L4.5,0.5 L5,3.5 L3.7,4.5 C4.4,6 5.8,7.5 7.5,8.3 L8.5,7 L11.5,7.5 L11.5,9.5 C11.5,10.8 10.5,11.5 9.5,11.5 C4.5,11 1,7.5 0.5,2.5 C0.5,1.5 1.2,0.5 2.5,0.5 Z"/></svg>+34 (91) 387-2265
      </div>
      <div class="contact__line">
        <svg viewBox="0 0 12 12" aria-hidden="true"><path d="M3,0 H9 V12 H3 Z M4,1.5 V8.5 H8 V1.5 Z"/></svg>+34 (646) 819-054
      </div>
    </div>
    <div class="email">
      <svg viewBox="0 0 11 9" aria-hidden="true"><path d="M0,0 H11 V9 H0 Z M1,1.2 L5.5,5 L10,1.2 Z"/></svg>labadal@velmorapartners.com
    </div>
  </section>

  <section class="card card--back">
    <div class="brand">velmora partners</div>
    <div class="website">www.velmora.com</div>
  </section>
</body>
</html>
```